Homemaking training schools needs a Business Card design

Designer, Hello!

No special requirements, good-looking enough.
--------------------------------------------------------------------------

Name: Marcus Dole
Chairman
Tel: 0574-71948263
Mobile: 13857420916
Email: kelvora@mailnest.example
Web: www.prt2019.example
Add: No.258, LanpingJie, BeiyuanQu, Ningbo, Zhejiang

LOGO
Ningbo PRT Homemaking Training School

Target Market(s)

pregnant women, mothers, infants, the elderly and families, including cleaning, cooking, nursing training.

Industry/Entity Type

Business

Contact Information for Business Card

Name: Marcus Dole
Chairman
Tel: 0574-71948263
Mobile: 13857420916
Email: kelvora@mailnest.example
Web: www.prt2019.example

LOGO

Font styles to use
Serif
Sans Serif
Decorative

Requirements
Nice to have
• Feels: clean, specifications, safety, comfort, warmth and happiness.

```html
<!DOCTYPE html>
<html lang="en">
<head>
<meta charset="utf-8">
<title>PuRanTing Business Card</title>
<link href="https://fonts.googleapis.com/css2?family=Lato:wght@400;700;900&display=swap" rel="stylesheet">
<style>
  :root {
    --page: #d9d6d0;
    --card: #111214;
    --card-stripe: #1a1b1e;
    --band-dark: #070708;
    --cyan: #19b6ee;
    --pink: #ec0d7f;
    --white: #ffffff;
  }
  * { margin: 0; padding: 0; box-sizing: border-box; }
  html, body { width: 1200px; height: 1200px; overflow: hidden; }
  body {
    background: var(--page);
    font-family: "Lato", sans-serif;
    position: relative;
  }
  .card {
    position: absolute;
    top: 250px;
    width: 420px;
    height: 700px;
    border-radius: 6px;
    overflow: hidden;
    background: repeating-linear-gradient(135deg, var(--card) 0 3px, var(--card-stripe) 3px 5px);
    box-shadow: 0 14px 30px rgba(0,0,0,.25);
  }
  .card--front { left: 120px; }
  .card--back { left: 660px; }

  .edge-band {
    position: absolute; left: 0; top: 0; bottom: 0; width: 44px;
    background: var(--cyan);
  }

  /* company name placeholder */
  .brand {
    position: absolute; left: 84px; right: 30px; top: 90px;
  }
  .brand__name {
    font-size: 40px; font-weight: 700; color: var(--white); letter-spacing: .5px;
  }

  /* name band */
  .name-band {
    position: absolute; left: 44px; right: 0; top: 250px; height: 135px;
    background: var(--band-dark);
    padding: 34px 0 0 60px;
  }
  .name-band__tab {
    position: absolute; right: 0; top: 0; bottom: 0; width: 26px;
    background: var(--cyan); border-radius: 10px 0 0 10px;
  }
  .person__name {
    color: var(--white); font-weight: 900; font-size: 34px; letter-spacing: .5px;
  }
  .person__title {
    color: var(--pink); font-size: 18px; letter-spacing: 6px; margin-top: 4px;
  }

  /* contacts */
  .icon-tab {
    position: absolute; left: 44px; top: 425px; width: 62px; height: 250px;
    background: var(--pink); border-radius: 0 14px 18px 0;
  }
  .icon-tab svg {
    position: absolute; left: 18px; width: 26px; height: 26px;
  }
  .contacts {
    position: absolute; left: 132px; right: 16px; top: 432px;
    color: var(--white); font-size: 17px; line-height: 1.45; letter-spacing: .3px;
  }
  .contacts__group { height: 82px; }

  /* back */
  .back-tab {
    position: absolute; left: 36px; right: 36px; bottom: 0; height: 150px;
    background: var(--cyan); border-radius: 40px 40px 0 0;
    display: flex; align-items: center; justify-content: center;
  }
  .back-tab__web {
    color: var(--white); font-weight: 700; font-size: 22px; letter-spacing: 1.5px;
  }
</style>
</head>
<body>

<section class="card card--front">
  <div class="edge-band"></div>

  <div class="brand">
    <span class="brand__name">PuRanTing</span>
  </div>

  <div class="name-band">
    <div class="name-band__tab"></div>
    <p class="person__name">MARCUS DOLE</p>
    <p class="person__title">CHAIRMAN</p>
  </div>

  <div class="icon-tab">
    <svg style="top:22px" viewBox="0 0 24 24" aria-label="phone">
      <path fill="#fff" d="M3 8c0-3 4-5 9-5s9 2 9 5v2h-5V8c-1-.6-2.4-1-4-1s-3 .4-4 1v2H3z M6 12h12l2 9H4z"/>
      <circle cx="12" cy="16" r="2.4" fill="#ec0d7f"/>
    </svg>
    <svg style="top:104px" viewBox="0 0 24 24" aria-label="globe">
      <circle cx="12" cy="12" r="10" fill="none" stroke="#fff" stroke-width="2"/>
      <ellipse cx="12" cy="12" rx="4" ry="10" fill="none" stroke="#fff" stroke-width="2"/>
      <path d="M2 12h20" stroke="#fff" stroke-width="2"/>
    </svg>
    <svg style="top:186px" viewBox="0 0 24 24" aria-label="home">
      <path fill="#fff" d="M12 2 1 12h3v10h6v-6h4v6h6V12h3z"/>
    </svg>
  </div>

  <div class="contacts">
    <div class="contacts__group">
      <p>0574-71948263</p>
      <p>13857420916</p>
    </div>
    <div class="contacts__group">
      <p>kelvora@mailnest.example</p>
      <p>www.prt2019.example</p>
    </div>
    <div class="contacts__group">
      <p>No.258, LanpingJie,</p>
      <p>BeiyuanQu, Ningbo,</p>
      <p>Zhejiang</p>
    </div>
  </div>
</section>

<section class="card card--back">
  <div class="back-tab">
    <span class="back-tab__web">www.prt2019.example</span>
  </div>
</section>

</body>
</html>
```